Laser Tattoo Removal Business Cards

We are looking for a professional business card design for a laser tattoo removal business. Ideally looking for a black business card design. The name of the business is Brightline Tattoo Removal. We place our cards at local tattoo shops so we ideally are looking for something trendy/edgy to draw both male and female clientele in.

Target Market(s)

Male/Female ages 18-60

Contact Information for Business Card

black background ideally.. hoping to stay within greys, whites and black

Font styles to use
Serif
Sans Serif

Colors
121212
a9a9a9
5c5c5c
f5f5f5
ffffff
7f7f7f
606060
848484
9d9d9d

Requirements
Must have
• Employee Info:
• Melissa Thornbury
• Chief Executive Offer
• m: 919.537.2846
• w: 919.362.4178
• f: 919.685.3907
• mthornbury@brightlinetattooremoval.example
• Address:
• 4615 Oakmere Pkwy, Suite 210
• Raleigh, NC 27654
• Website:
• www.brightlinetattooremoval.example
Nice to have
• Myabe business name on back or logo on back and employee info on the front

```html
<!DOCTYPE html>
<html lang="en">
<head>
<meta charset="utf-8">
<title>Brightline Tattoo Removal — Business Cards</title>
<link href="https://fonts.googleapis.com/css2?family=Roboto:wght@400;500;700&display=swap" rel="stylesheet">
<style>
  :root {
    --card-black: #121212;
    --backdrop: #3a3431;
    --white: #ffffff;
    --off-white: #f5f5f5;
    --grey-light: #a9a9a9;
    --grey-mid: #7f7f7f;
    --grey-dark: #5c5c5c;
  }
  html, body {
    margin: 0;
    padding: 0;
    width: 1200px;
    height: 769px;
    overflow: hidden;
    background: var(--backdrop);
    font-family: "Roboto", Arial, sans-serif;
  }
  .canvas {
    position: relative;
    width: 1200px;
    height: 769px;
  }
  .card {
    position: absolute;
    top: 230px;
    width: 540px;
    height: 309px;
    background: var(--card-black);
    box-shadow: 0 10px 30px rgba(0,0,0,0.45);
    color: var(--off-white);
  }
  .card--front { left: 40px; }
  .card--back { left: 620px; }

  /* front */
  .brand {
    position: absolute;
    text-align: center;
    color: var(--white);
  }
  .card--front .brand {
    left: 0;
    top: 0;
    width: 270px;
    height: 309px;
    display: flex;
    flex-direction: column;
    justify-content: center;
    align-items: center;
  }
  .brand__name {
    font-weight: 500;
    font-size: 36px;
    letter-spacing: 3px;
    line-height: 1;
  }
  .brand__tagline {
    margin-top: 14px;
    font-weight: 500;
    font-size: 14px;
    letter-spacing: 3px;
    display: flex;
    align-items: center;
    gap: 8px;
  }
  .brand__rule {
    display: inline-block;
    width: 14px;
    height: 1px;
    background: var(--white);
  }
  .divider {
    position: absolute;
    left: 270px;
    top: 40px;
    width: 1px;
    height: 229px;
    background: var(--grey-dark);
  }
  .contact {
    position: absolute;
    left: 294px;
    top: 52px;
    width: 240px;
    font-size: 12px;
    line-height: 1.25;
    color: var(--off-white);
  }
  .contact__name {
    font-weight: 700;
    font-size: 17px;
    letter-spacing: 0.3px;
    color: var(--white);
  }
  .contact__title {
    font-size: 12.5px;
    margin-bottom: 8px;
  }
  .contact__address { margin-bottom: 8px; font-size: 12.5px; }
  .contact__list {
    list-style: none;
    margin: 0;
    padding: 0;
  }
  .contact__list li {
    display: flex;
    align-items: center;
    gap: 7px;
    height: 16px;
    font-size: 12px;
    white-space: nowrap;
  }
  .contact__list li.is-small { font-size: 10.2px; }
  .icon { width: 11px; height: 11px; flex: none; fill: var(--off-white); }

  /* back */
  .card--back .brand {
    left: 0;
    top: 70px;
    width: 540px;
  }
  .card--back .brand__name {
    font-size: 40px;
    color: var(--off-white);
  }
  .card--back .brand__tagline { justify-content: center; color: var(--grey-light); }
  .card--back .brand__tagline .brand__rule { background: var(--grey-light); }
  .website {
    position: absolute;
    left: 0;
    top: 236px;
    width: 540px;
    text-align: center;
    font-size: 12px;
    letter-spacing: 3px;
    color: var(--off-white);
  }
</style>
</head>
<body>
<div class="canvas">

  <section class="card card--front" aria-label="Business card front">
    <div class="brand">
      <div class="brand__name">BRIGHTLINE</div>
      <div class="brand__tagline"><span class="brand__rule"></span>TATTOO REMOVAL<span class="brand__rule"></span></div>
    </div>
    <div class="divider"></div>
    <div class="contact">
      <div class="contact__name">MELISSA THORNBURY</div>
      <div class="contact__title">Chief Executive Offer</div>
      <div class="contact__address">4615 Oakmere Pkwy, Suite 210<br>Raleigh, NC 27654</div>
      <ul class="contact__list">
        <li>
          <svg class="icon" viewBox="0 0 12 12"><path d="M2.5 1 L4.5 1 L5.2 3.4 L4 4.3 C4.6 5.7 6.3 7.4 7.7 8 L8.6 6.8 L11 7.5 L11 9.5 C11 10.4 10.3 11 9.5 11 C5 10.7 1.3 7 1 2.5 C1 1.7 1.6 1 2.5 1 Z"/></svg>
          919.362.4178
        </li>
        <li>
          <svg class="icon" viewBox="0 0 12 12"><path d="M3.5 0.5 H8.5 A1 1 0 0 1 9.5 1.5 V10.5 A1 1 0 0 1 8.5 11.5 H3.5 A1 1 0 0 1 2.5 10.5 V1.5 A1 1 0 0 1 3.5 0.5 Z M3.7 1.8 V9.2 H8.3 V1.8 Z M5.4 9.8 H6.6 V10.6 H5.4 Z"/></svg>
          919.537.2846
        </li>
        <li>
          <svg class="icon" viewBox="0 0 12 12"><path d="M3 1 H8 V4 H3 Z M1 4.5 H11 V10 H9 V8 H3 V10 H1 Z M3.5 8.5 H8.5 V11 H3.5 Z"/></svg>
          919.685.3907
        </li>
        <li class="is-small">
          <svg class="icon" viewBox="0 0 12 12"><path d="M0.5 2.5 H11.5 V9.5 H0.5 Z M1.3 3.2 L6 6.6 L10.7 3.2 Z" fill-rule="evenodd"/></svg>
          mthornbury@brightlinetattooremoval.example
        </li>
        <li class="is-small">
          <svg class="icon" viewBox="0 0 12 12"><circle cx="6" cy="6" r="5.5"/><path d="M0.5 6 H11.5 M6 0.5 C3.5 3 3.5 9 6 11.5 M6 0.5 C8.5 3 8.5 9 6 11.5" stroke="#121212" stroke-width="0.9" fill="none"/></svg>
          www.brightlinetattooremoval.example
        </li>
      </ul>
    </div>
  </section>

  <section class="card card--back" aria-label="Business card back">
    <div class="brand">
      <div class="brand__name">BRIGHTLINE</div>
      <div class="brand__tagline"><span class="brand__rule"></span>TATTOO REMOVAL<span class="brand__rule"></span></div>
    </div>
    <div class="website">www.brightlinetattooremoval.example</div>
  </section>

</div>
</body>
</html>
```